Wine Label Design-Hollow Creek Vineyard

Hollow Creek Vineyard is in the Barossa Valley in South Australia. The Barossa is recognized as Australia's premier wine region, producing Australia's icon wines and some " new takes on traditional".
This family owned and operated vineyard grows some exceptionally high quality fruit. Most of the fruit is sold and used for some of Australia's most iconic wines. Small quantities are retained by the owners for some wines with very limited availability. (Wines were previously sold as Brackwell Vineyards Hollow Creek ( Shiraz, Cabernet etc).

The wines will in the future be labeled simply ‘Hollow Creek Vineyard’. The label will launch this new identity for the single family single vineyard and its high quality wines which are a true expression of the vineyard and derive from the Hollow Creek common to this ancient area (800-2000 million years old).
The label should reflect
• Single vineyard, family owned
• vines in very old rock & soils
• High quality & reliability
• Edgy but true, design based thinking (Please note:blue is generally seen as an unacceptable colour for a wine label?? Don’t ask me why)

The wines will be sold mostly direct in Australia ( ie not through retail stores), with limited export to Asia, Scandinavia and Canada.
There are three quality levels and price points in the portfolio
1. Entry level premium for everyday drinking for discriminating drinkers-approx AUD20
2. Super Premium-approx AUD30
3. Limited Release ultlra premium-AUD75-90?
We envisage three variations on the label but with an obvious & common design element. This design element should be able to be used for corporate identification and promotion
The paper stock will be waterproof and self adhesive. Our preference is for designs that engage the user by appealing to both sight and touch. It is preferred that textures be added eg embossing, high build varnish etc-rather than be a facet of the stock itself.
For information on statutory label requirements refer to www.vintnerregistry-example.com . In brief
o Front label need not show any mandatory information. However we would prefer Variety, Barossa Valley, Year and alcohol to be shown on the front label
o Back label should show all mandatories and allow for a bar code
Updates

Project Deadline Extended
Reason: I've had a problem with my wireless broadband account and reception has been intermittent to say the least to the extent that I switched off at the weekend. Just going downtown now for a 'polite discussion' with my service provider.

Project Deadline Extended
Reason: I have receiver insufficient designs of quality which we would consider. Too many designs have a "cut and paste" appearance - too few exhibit an original art/design element which truly identifies the product.

Gals & Guys

most of the designs submitted lack punch and originality and are totally unmemorable.
Please-get on Searcho or whatever enter "Wine Label Designs" and do some research b4 u waste your time and mine. Formulaic cut and paste will not win the day. That's not to say that cut and paste can't work-but it must have some originality, impact and command attention. Please surprise me.

Following on from a question from a designer about who is our competition and what we are looking for I sent the following 
"I don't think I can add anything new. Read the brief and comments again and research wine labels on the web. In 30 minutes you'll get a good idea of the creative edgy designs in the industry. There are a plethora of collections. Our competition-anyone with a label. In 2010 there were over 2400 "producers" in other words 2400 producers with at least one label. In fact there are over 25000 Australian wines and then the numerous imported wines.

Target Market(s)

$20 people who budget everyday but have graduated from drinking 'entry level' wines. These people will likely fit into Cat. (b) in the $30 wine

$30 (a) will not over-compromise on some everyday discretionary expenditure.(b) might buy for special occasions

$70-$90 Professional/successful people with high disposable/discretionary income not particularly worried about recession. wine geeks.

Industry/Entity Type

Retail

Requirements
Must have
• identifiable element across range of wines

```html
<!DOCTYPE html>
<html lang="en">
<head>
<meta charset="utf-8">
<title>Hollow Creek Vineyard – Front Label</title>
<link rel="stylesheet" href="https://fonts.googleapis.com/css2?family=Fondamento:ital@0;1&family=Libre+Baskerville&display=swap">
<style>
  :root {
    --page-bg: #e4e4e6;
    --label-black: #0f0d0a;
    --label-umber: #3a3024;
    --label-bronze: #4a3d2c;
    --gold: #c9b56a;
    --gold-soft: #a8955a;
    --gold-line: rgba(176, 152, 92, 0.7);
    --ornament-tone: rgba(150, 128, 78, 0.35);
    --serif-grey: #b5ab92;
  }
  html, body {
    margin: 0;
    padding: 0;
    width: 1200px;
    height: 1200px;
    overflow: hidden;
    background: var(--page-bg);
  }
  .canvas {
    position: relative;
    width: 1200px;
    height: 1200px;
    background: var(--page-bg);
  }
  .wine-label {
    position: absolute;
    left: 210px;
    top: 50px;
    width: 780px;
    height: 1100px;
    background: var(--label-black);
    box-shadow: 12px 14px 22px rgba(0, 0, 0, 0.35);
    overflow: hidden;
  }
  .label-texture {
    position: absolute;
    inset: 0;
    background: linear-gradient(165deg, var(--label-bronze) 0%, var(--label-umber) 35%, var(--label-black) 60%, var(--label-umber) 100%);
  }
  .label-border {
    position: absolute;
    inset: 6px;
    border: 3px solid var(--gold-line);
  }
  .title-frame {
    position: absolute;
    left: 40px;
    top: 285px;
    width: 700px;
    height: 350px;
  }
  .title-panel {
    position: absolute;
    left: 20px;
    right: 20px;
    top: 28px;
    bottom: 28px;
    background: rgba(40, 32, 22, 0.45);
    border: 3px solid var(--gold-line);
  }
  .title-panel::after {
    content: "";
    position: absolute;
    inset: 10px;
    border: 1.5px solid var(--gold-line);
  }
  .filigree-corner {
    position: absolute;
    width: 120px;
    height: 70px;
    background: var(--ornament-tone);
  }
  .filigree-corner.top-left { left: 0; top: 0; }
  .filigree-corner.top-right { right: 0; top: 0; }
  .filigree-corner.bottom-left { left: 0; bottom: 0; }
  .filigree-corner.bottom-right { right: 0; bottom: 0; }
  .vineyard-name {
    position: absolute;
    left: 0;
    right: 0;
    top: 72px;
    margin: 0;
    text-align: center;
    font-family: "Fondamento", cursive;
    font-style: italic;
    font-weight: 400;
    font-size: 92px;
    line-height: 104px;
    color: var(--gold);
    text-shadow: 2px 3px 3px rgba(0, 0, 0, 0.8);
  }
  .region {
    position: absolute;
    left: 0;
    right: 0;
    top: 745px;
    margin: 0;
    text-align: center;
    font-family: "Libre Baskerville", serif;
    font-size: 46px;
    color: var(--serif-grey);
  }
  .vintage-ribbon {
    position: absolute;
    left: 100px;
    top: 930px;
    width: 580px;
    height: 90px;
    background: linear-gradient(90deg, rgba(150, 128, 78, 0.15), var(--ornament-tone) 50%, rgba(150, 128, 78, 0.15));
  }
  .vintage-year {
    position: absolute;
    left: 0;
    right: 0;
    top: 25px;
    margin: 0;
    text-align: center;
    font-family: "Fondamento", cursive;
    font-style: italic;
    font-size: 34px;
    color: var(--gold-soft);
  }
</style>
</head>
<body>
<main class="canvas">
  <section class="wine-label">
    <div class="label-texture" role="img" aria-label="Weathered dark brown and black distressed stone texture across the label"></div>
    <div class="label-border"></div>

    <div class="title-frame">
      <div class="filigree-corner top-left" role="img" aria-label="Gold filigree flourish"></div>
      <div class="filigree-corner top-right" role="img" aria-label="Gold filigree flourish"></div>
      <div class="filigree-corner bottom-left" role="img" aria-label="Gold filigree flourish"></div>
      <div class="filigree-corner bottom-right" role="img" aria-label="Gold filigree flourish"></div>
      <div class="title-panel"></div>
      <h1 class="vineyard-name">Hollow Creek<br>Vineyard</h1>
    </div>

    <p class="region">Barossa Valley</p>

    <div class="vintage-ribbon" role="img" aria-label="Gold scroll ribbon carrying the vintage year">
      <p class="vintage-year">Vintage 2012</p>
    </div>
  </section>
</main>
</body>
</html>
```